Wine Label Design-Hollow Creek Vineyard

Hollow Creek Vineyard is in the Barossa Valley in South Australia. The Barossa is recognized as Australia's premier wine region, producing Australia's icon wines and some " new takes on traditional".
This family owned and operated vineyard grows some exceptionally high quality fruit. Most of the fruit is sold and used for some of Australia's most iconic wines. Small quantities are retained by the owners for some wines with very limited availability. (Wines were previously sold as Brackwell Vineyards Hollow Creek ( Shiraz, Cabernet etc).

The wines will in the future be labeled simply ‘Hollow Creek Vineyard’. The label will launch this new identity for the single family single vineyard and its high quality wines which are a true expression of the vineyard and derive from the Hollow Creek common to this ancient area (800-2000 million years old).
The label should reflect
• Single vineyard, family owned
• vines in very old rock & soils
• High quality & reliability
• Edgy but true, design based thinking (Please note:blue is generally seen as an unacceptable colour for a wine label?? Don’t ask me why)

The wines will be sold mostly direct in Australia ( ie not through retail stores), with limited export to Asia, Scandinavia and Canada.
There are three quality levels and price points in the portfolio
1. Entry level premium for everyday drinking for discriminating drinkers-approx AUD20
2. Super Premium-approx AUD30
3. Limited Release ultlra premium-AUD75-90?
We envisage three variations on the label but with an obvious & common design element. This design element should be able to be used for corporate identification and promotion
The paper stock will be waterproof and self adhesive. Our preference is for designs that engage the user by appealing to both sight and touch. It is preferred that textures be added eg embossing, high build varnish etc-rather than be a facet of the stock itself.
For information on statutory label requirements refer to www.vintnerregistry-example.com . In brief
o Front label need not show any mandatory information. However we would prefer Variety, Barossa Valley, Year and alcohol to be shown on the front label
o Back label should show all mandatories and allow for a bar code
Updates

Project Deadline Extended
Reason: I've had a problem with my wireless broadband account and reception has been intermittent to say the least to the extent that I switched off at the weekend. Just going downtown now for a 'polite discussion' with my service provider.

Project Deadline Extended
Reason: I have receiver insufficient designs of quality which we would consider. Too many designs have a "cut and paste" appearance - too few exhibit an original art/design element which truly identifies the product.

Gals & Guys

most of the designs submitted lack punch and originality and are totally unmemorable.
Please-get on Searcho or whatever enter "Wine Label Designs" and do some research b4 u waste your time and mine. Formulaic cut and paste will not win the day. That's not to say that cut and paste can't work-but it must have some originality, impact and command attention. Please surprise me.

Following on from a question from a designer about who is our competition and what we are looking for I sent the following 
"I don't think I can add anything new. Read the brief and comments again and research wine labels on the web. In 30 minutes you'll get a good idea of the creative edgy designs in the industry. There are a plethora of collections. Our competition-anyone with a label. In 2010 there were over 2400 "producers" in other words 2400 producers with at least one label. In fact there are over 25000 Australian wines and then the numerous imported wines.

Target Market(s)

$20 people who budget everyday but have graduated from drinking 'entry level' wines. These people will likely fit into Cat. (b) in the $30 wine

$30 (a) will not over-compromise on some everyday discretionary expenditure.(b) might buy for special occasions

$70-$90 Professional/successful people with high disposable/discretionary income not particularly worried about recession. wine geeks.

Industry/Entity Type

Retail

Requirements
Must have
• identifiable element across range of wines

```html
<!DOCTYPE html>
<html lang="en">
<head>
<meta charset="utf-8">
<title>Hollow Creek Vineyards – Wine Labels</title>
<link rel="stylesheet" href="https://fonts.googleapis.com/css2?family=Source+Sans+3:wght@700&display=swap">
<style>
  :root {
    --page: #ffffff;
    --frame: #5e2614;
    --frame-light: #7a3a22;
    --frame-dark: #46190c;
    --field-light: #f6f1a6;
    --field-mid: #efe46a;
    --field-edge: #e2cf34;
    --field-line: rgba(255, 255, 255, 0.75);
    --brown: #7a3b1c;
    --ink: #1a1208;
    --plum: #6a2a6e;
    --violet: #6a34a0;
    --vine: #7e3f22;
    --box: #ffffff;
  }
  * { box-sizing: border-box; margin: 0; padding: 0; }
  html, body { width: 1200px; height: 847px; overflow: hidden; background: var(--page); }
  body { font-family: "Source Sans 3", "Myriad Pro", Arial, sans-serif; font-weight: 700; }
  .canvas { position: relative; width: 1200px; height: 847px; }

  .label {
    position: absolute;
    width: 455px;
    height: 682px;
    background: linear-gradient(135deg, var(--frame-light) 0%, var(--frame) 45%, var(--frame-dark) 100%);
    border: 2px solid var(--frame-dark);
    padding: 19px;
  }
  .label--front { left: 80px; top: 100px; }
  .label--back { left: 682px; top: 98px; }
  .label__field {
    position: relative;
    width: 100%;
    height: 100%;
    outline: 1px dashed var(--field-line);
    outline-offset: -1px;
    background: radial-gradient(ellipse at 50% 45%, var(--field-light) 0%, var(--field-mid) 60%, var(--field-edge) 100%);
  }
  .label__field > * { position: absolute; }

  .rule { height: 4px; background: var(--brown); }

  /* Front label */
  .brand-mark {
    left: 40px; top: 24px;
    width: 56px; height: 56px;
    border-radius: 50%;
    background: var(--plum);
  }
  .brand-name {
    left: 104px; top: 44px;
    font-size: 23px; letter-spacing: 0.6px;
    color: var(--brown); white-space: nowrap;
  }
  .brand-sub {
    left: 0; right: 0; top: 79px;
    text-align: center; font-size: 23px; letter-spacing: 0.4px;
    color: var(--brown);
  }
  .rule--brand-left { left: 0; width: 110px; top: 93px; }
  .rule--brand-right { left: 306px; width: 107px; top: 93px; }
  .vine-art {
    left: 45px; top: 220px; width: 318px; height: 236px;
    border-radius: 22px;
    background:
      radial-gradient(circle at 83% 64%, var(--plum) 0 17%, transparent 18%),
      linear-gradient(120deg, var(--violet) 0%, var(--vine) 55%, var(--plum) 100%);
  }
  .region {
    left: 0; right: 0; top: 502px;
    text-align: center; font-size: 27px; color: var(--brown);
  }
  .vintage {
    left: 0; right: 0; top: 541px;
    text-align: center; font-size: 31px; color: var(--brown);
  }
  .rule--vintage-left { left: 19px; width: 132px; top: 561px; }
  .rule--vintage-right { left: 269px; width: 126px; top: 561px; }
  .variety {
    left: 0; right: 0; top: 592px;
    text-align: center; font-size: 25px; color: var(--brown);
  }

  /* Back label */
  .back-title {
    left: 0; right: 0; top: 11px;
    text-align: center; font-size: 18.5px; font-weight: 700; color: var(--brown);
  }
  .story {
    left: 0; right: 0; top: 54px;
    text-align: center; white-space: nowrap;
    font-size: 14px; line-height: 19.4px; color: var(--ink);
  }
  .story p + p { margin-top: 3px; }
  .story__initial { font-size: 19px; line-height: 0; color: var(--brown); }
  .standard-drinks {
    left: 0; right: 0; top: 423px;
    text-align: center; font-size: 17.5px; color: var(--brown);
  }
  .statutory {
    left: 3px; top: 452px;
    list-style: none; font-size: 14px; line-height: 19.3px; color: var(--ink);
    white-space: nowrap;
  }
  .statutory__producer { color: var(--brown); }
  .barcode-space {
    left: 260px; top: 495px; width: 137px; height: 108px;
    background: var(--box); border: 2px solid var(--ink);
  }
</style>
</head>
<body>
<main class="canvas">

  <section class="label label--front" aria-label="Front label">
    <div class="label__field">
      <span class="brand-mark" aria-hidden="true"></span>
      <div class="brand-name">HOLLOW CREEK</div>
      <div class="rule rule--brand-left"></div>
      <div class="brand-sub">VINEYARDS</div>
      <div class="rule rule--brand-right"></div>
      <div class="vine-art" role="img" aria-label="Illustration of a curling brown grapevine with purple leaves and a bunch of grapes"></div>
      <div class="region">Barossa Valley</div>
      <div class="rule rule--vintage-left"></div>
      <div class="vintage">2012</div>
      <div class="rule rule--vintage-right"></div>
      <div class="variety">Bourdeaux</div>
    </div>
  </section>

  <section class="label label--back" aria-label="Back label">
    <div class="label__field">
      <h2 class="back-title">Bordeaux * 2012 * Barossa Valley</h2>
      <div class="story">
        <p><span class="story__initial">O</span>ur wines are planted on areas which<br>are characterized by enormous<br>quantities of shattered shale, slate, and<br>limestone based rock.</p>
        <p><span class="story__initial">T</span>he shattered shale and limestone<br>based rocks give name to our premium<br>line. They are present throughout the<br>vineyards and are a major component<br>of the unique nature of the differing<br>terroirs and contribute to the wines<br>with tight structure and minerality yet<br>abundant and generous fruit.</p>
        <p><span class="story__initial">O</span>ur wines drink well from release.<br>Reds from 2 to 3 years from vintage.<br>Cellaring potential varies between<br>vintages but as a general rule they<br>drink best in the range of 6 to 12 years<br>of age</p>
      </div>
      <div class="standard-drinks">Contains approx. 8.3 Standard Drinks</div>
      <ul class="statutory">
        <li>750mL</li>
        <li>Wine Of Australia</li>
        <li>13.5% ALC/VOL</li>
        <li>CONTAINS SULFATES</li>
        <li>PRODUCED WITH MILK PRODUCTS</li>
        <li class="statutory__producer">Hollow Creek Vineyards</li>
        <li>Lot 7 Ferngate Road, Marlowe, SA</li>
        <li>5399 Australia</li>
      </ul>
      <div class="barcode-space" aria-label="Space reserved for bar code"></div>
    </div>
  </section>

</main>
</body>
</html>
```